Building company buisness cards

We are looking for a sharp modern new look for our business cards.
We are a New Zealand based company that specialises in house and land packages.
We have attached a photo of the current logo and would like to see if it can be improved somehow if needed.
We are open to any colours but we have chosen green at this stage.
Feel free to change the font and make the logo smarter looking.
Play with the colours and see what looks best.

We want a card that looks so good know one will want to throw it away!

Target Market(s)

Home buyers

Industry/Entity Type

Building

Contact Information for Business Card

Derek Tolvane
0217394062
dtolvane@quillmarkhomesteads.co.nz
quillmarkhomesteads.co.nz

Font styles to use
Serif
Sans Serif

Colors

Designer to choose colors to be used in the design.

Requirements
Must have
• Logo and company name on one side, details on the other side
Nice to have
• Color codes for the original green are HEX #4a8028, RGB(74,128,40), CMYK(42,0,69,50)
• Round corners, Raised and/or spot UV

```html
<!DOCTYPE html>
<html lang="en">
<head>
<meta charset="utf-8">
<title>Quillmark Homesteads – Business Cards</title>
<link href="https://fonts.googleapis.com/css2?family=Lato:wght@400;700;900&display=swap" rel="stylesheet">
<style>
  :root {
    --brand-green: #4a8028;
    --card-grey: #e8e8e8;
    --ink: #2a2a2a;
    --white: #ffffff;
    --stage: #5b5b5b;
  }
  * { margin: 0; padding: 0; box-sizing: border-box; }
  html, body { width: 1200px; height: 802px; overflow: hidden; }
  body {
    position: relative;
    background: var(--stage);
    font-family: "Lato", Arial, sans-serif;
  }
  .card {
    position: absolute;
    top: 274px;
    width: 443px;
    height: 265px;
    overflow: hidden;
    box-shadow: 2px 3px 6px rgba(0,0,0,0.35);
  }
  .card--details { left: 136px; background: var(--card-grey); }
  .card--brand { left: 624px; background: var(--brand-green); }

  .family-art {
    position: absolute;
    left: 0; top: 0;
    width: 234px; height: 100%;
    background: linear-gradient(90deg,
      var(--brand-green) 0%,
      #6f9a55 45%,
      #cfdcc6 73%,
      var(--card-grey) 100%);
  }
  .holder-name {
    position: absolute;
    right: 21px;
    top: 142px;
    color: var(--brand-green);
    font-weight: 700;
    font-size: 16px;
    letter-spacing: 0.2px;
    text-transform: uppercase;
  }
  .contact-list {
    position: absolute;
    right: 21px;
    top: 186px;
    list-style: none;
    text-align: right;
  }
  .contact-list li {
    display: flex;
    justify-content: flex-end;
    align-items: center;
    gap: 4px;
    height: 16px;
    font-size: 11.5px;
    color: var(--ink);
  }
  .contact-icon { width: 9px; height: 9px; flex: none; }

  .brand-mark {
    position: absolute;
    left: 199px;
    top: 66px;
    width: 45px;
    height: 45px;
    border-radius: 50%;
    background: var(--white);
  }
  .brand-name {
    position: absolute;
    left: 0; right: 0;
    text-align: center;
    color: var(--white);
    font-weight: 900;
    letter-spacing: -0.3px;
    line-height: 1;
  }
  .brand-name--top { top: 131px; font-size: 26px; }
  .brand-name--bottom { top: 160px; font-size: 35px; }
  .brand-rule {
    position: absolute;
    left: 190px;
    top: 200px;
    width: 63px;
    height: 1px;
    background: rgba(255,255,255,0.45);
  }
</style>
</head>
<body>
  <section class="card card--details">
    <div class="family-art" role="img" aria-label="Illustration of a family of three holding hands, white figures on green"></div>
    <p class="holder-name">Derek Tolvane</p>
    <ul class="contact-list">
      <li>0217394062
        <svg class="contact-icon" viewBox="0 0 10 10" aria-hidden="true"><path d="M1 4 Q5 0 9 4 L8 5 L6.5 4 V3 Q5 2.4 3.5 3 V4 L2 5 Z M2.5 5.5 H7.5 L8.5 9 H1.5 Z" fill="var(--brand-green)"/></svg>
      </li>
      <li>dtolvane@quillmarkhomesteads.co.nz
        <svg class="contact-icon" viewBox="0 0 10 10" aria-hidden="true"><rect x="0.5" y="2" width="9" height="6.5" fill="var(--brand-green)"/><path d="M0.8 2.4 L5 5.8 L9.2 2.4" stroke="var(--card-grey)" stroke-width="0.9" fill="none"/></svg>
      </li>
      <li>www.quillmarkhomesteads.co.nz
        <svg class="contact-icon" viewBox="0 0 10 10" aria-hidden="true"><circle cx="5" cy="5" r="4.6" fill="var(--brand-green)"/><path d="M2 3.5 Q4 3 4.5 5 Q6 5.5 5.5 8 M6.5 2 Q8 3.5 7.5 5" stroke="var(--card-grey)" stroke-width="0.8" fill="none"/></svg>
      </li>
    </ul>
  </section>

  <section class="card card--brand">
    <div class="brand-mark" aria-hidden="true"></div>
    <p class="brand-name brand-name--top">quillmark</p>
    <p class="brand-name brand-name--bottom">homesteads.</p>
    <div class="brand-rule"></div>
  </section>
</body>
</html>
```